Business card design for new eCommerce site focusing on integrity and strong businsess tactics

We need a business card that will stand out and be memorable. Something with color that matches our company logo colors. Think high end version of Pactivo. There are 2 logos provided. The parent company is called Amber Ledge Partners and we are presenting a new and very exciting eCommerce site called BrightHarborTrade.example.

Target Market(s)

Our target markets are in the Activities, Food and Beverage, Health and Beauty

Industry/Entity Type

Marketing

Contact Information for Business Card

We have 4 members that need cards...I will provide all info to the winner of the design contest
Business Address is
4870 West 63rd Avenue, Suite C207
Phoenix AZ 85731

Font styles to use
Serif
Sans Serif

Colors

Designer to choose colors to be used in the design.

Requirements
Must have
• The card must be memorable...should be unique in design but must exude integrity and be playful .
• I have provided several colors or our parent company...please feel free to use which ever
Nice to have
• I will leave this up to you. Feel free to use other images of your choosing that wraps around our client.....Activities, Dining, Health, Beauty
Should not have
• just dont be boring

```html
<!DOCTYPE html>
<html lang="en">
<head>
<meta charset="utf-8">
<title>BrightHarborTrade business card</title>
<link href="https://fonts.googleapis.com/css2?family=Questrial&display=swap" rel="stylesheet">
<style>
  :root {
    --bg: #2c2c2e;
    --card: #f7f7f7;
    --blue: #2a7fb3;
    --green: #78bd3f;
    --text: #5a5a5a;
  }
  * { margin: 0; padding: 0; box-sizing: border-box; }
  html, body { width: 1200px; height: 834px; overflow: hidden; }
  body {
    background: var(--bg);
    font-family: "Questrial", "Century Gothic", sans-serif;
    display: flex; flex-direction: column; align-items: center; justify-content: center;
    gap: 50px;
  }
  .card {
    position: relative; width: 600px; height: 343px;
    background: var(--card); overflow: hidden;
    box-shadow: 0 10px 30px rgba(0,0,0,.45);
  }
  .card svg.shape { position: absolute; inset: 0; width: 100%; height: 100%; z-index: 0; }
  .brand, .partner, .contact { z-index: 1; white-space: nowrap; }
  .brand { position: absolute; display: flex; align-items: center; gap: 12px; }
  .brand-dot { width: 30px; height: 30px; border-radius: 50%; background: var(--blue); flex: none; }
  .brand-name { font-size: 26px; color: var(--green); line-height: 1; }
  .brand-tag { font-size: 12px; color: var(--text); letter-spacing: .8px; margin-top: 6px; }
  .front .brand { left: 60px; top: 95px; }
  .partner { position: absolute; right: 30px; top: 22px; display: flex; flex-direction: column; align-items: center; gap: 6px; }
  .partner-dot { width: 48px; height: 48px; border-radius: 50%; background: var(--green); }
  .partner-name { font-size: 12px; color: var(--green); }
  .back .brand { left: 40px; top: 190px; gap: 10px; }
  .back .brand-dot { width: 24px; height: 24px; }
  .back .brand-name { font-size: 20px; }
  .back .brand-tag { font-size: 10px; letter-spacing: .5px; margin-top: 5px; }
  .contact { position: absolute; left: 355px; top: 70px; color: var(--text); font-size: 11.5px; line-height: 1.6; }
  .contact-name { color: var(--blue); font-size: 19px; letter-spacing: .5px; }
  .contact-role { color: var(--green); font-size: 14px; margin-bottom: 12px; }
  .contact-address { margin-bottom: 10px; }
  .contact-line { display: flex; align-items: center; gap: 8px; }
  .contact-line svg { width: 12px; height: 12px; flex: none; }
</style>
</head>
<body>

<section class="card front">
  <svg class="shape" viewBox="0 0 600 343" preserveAspectRatio="none">
    <path d="M0 268 C200 268 300 233 380 173 C450 121 500 105 600 103 L600 343 L0 343 Z" fill="var(--green)"/>
    <path d="M0 275 C200 275 300 240 380 180 C450 128 500 112 600 110 L600 343 L0 343 Z" fill="#fff"/>
    <path d="M0 279 C200 279 304 244 384 184 C454 132 504 116 600 114 L600 343 L0 343 Z" fill="var(--blue)"/>
  </svg>
  <div class="brand">
    <span class="brand-dot"></span>
    <div>
      <div class="brand-name">BrightHarborTrade.example</div>
      <div class="brand-tag">Activities-Dining-Health-Beauty</div>
    </div>
  </div>
  <div class="partner">
    <span class="partner-dot"></span>
    <span class="partner-name">Amber Ledge Partners</span>
  </div>
</section>

<section class="card back">
  <svg class="shape" viewBox="0 0 600 343" preserveAspectRatio="none">
    <path d="M330 0 L600 0 L600 90 C540 40 440 20 330 0 Z" fill="var(--blue)"/>
    <path d="M0 250 C40 300 120 330 230 343 L0 343 Z" fill="var(--green)"/>
  </svg>
  <div class="brand">
    <span class="brand-dot"></span>
    <div>
      <div class="brand-name">BrightHarborTrade.example</div>
      <div class="brand-tag">Activities-Dining-Health-Beauty</div>
    </div>
  </div>
  <div class="contact">
    <div class="contact-name">DANA WHITFIELD</div>
    <div class="contact-role">President</div>
    <div class="contact-address">4870 West 63rd Avenue, Suite C207<br>Phoenix AZ 85731</div>
    <div class="contact-line">
      <svg viewBox="0 0 12 12"><path d="M2 1 L4.5 1 L5.5 3.5 L4 4.5 C4.7 6 6 7.3 7.5 8 L8.5 6.5 L11 7.5 L11 10 C6 10.5 1.5 6 2 1 Z" fill="var(--green)"/></svg>
      555-014-2260
    </div>
    <div class="contact-line">
      <svg viewBox="0 0 12 12"><rect x="1" y="2.5" width="10" height="7" fill="none" stroke="var(--green)" stroke-width="1.3"/><path d="M1 2.5 L6 6.5 L11 2.5" fill="none" stroke="var(--green)" stroke-width="1.3"/></svg>
      dana@brightharbortrade.example
    </div>
    <div class="contact-line">
      <svg viewBox="0 0 12 12"><circle cx="6" cy="6" r="4.8" fill="none" stroke="var(--green)" stroke-width="1.3"/><path d="M1.2 6 H10.8 M6 1.2 C3.8 4 3.8 8 6 10.8 M6 1.2 C8.2 4 8.2 8 6 10.8" fill="none" stroke="var(--green)" stroke-width="1"/></svg>
      www.brightharbortrade.example
    </div>
  </div>
</section>

</body>
</html>
```